TolVex BIM business website

I have a logo design and business card concept is ongoing at this point, but i need a website design based on VDC or BIM ("Virtual Building and Construction" or "Building Information Modeling") that will stand out for the quality and concept that we provide. I am a consultant providing training and production work for Strukta (Quorvane application <where most of the overview can be obtained>). We are providing BIM production and coordination services as well. I can fill in the meat but I need an open development website. Currently, just obtaining a domain so it can be included on a business card is the quickest objective, then developing the content and launching it.

```html
<!DOCTYPE html>
<html lang="en">
<head>
<meta charset="utf-8">
<title>TolVex BIM Consulting</title>
<link rel="stylesheet" href="https://fonts.googleapis.com/css2?family=Montserrat:wght@600;700;800;900&family=Arimo:wght@400;700&display=swap">
<style>
:root{
  --navy:#1f2a5c;
  --orange:#f5a83a;
  --grey-band:#f4f4f4;
  --text:#4a4a4a;
  --footer:#3a3a3a;
  --white:#ffffff;
}
*{box-sizing:border-box;margin:0;padding:0}
html,body{width:1200px;height:3041px;overflow:hidden;background:var(--white)}
body{position:relative;font-family:"Arimo",Arial,sans-serif;color:var(--text)}
.abs{position:absolute}
.heading{font-family:"Montserrat",Arial,sans-serif;font-weight:800;color:var(--navy);letter-spacing:.5px}
.btn{position:absolute;background:var(--orange);color:var(--white);font-family:"Montserrat",Arial,sans-serif;font-weight:700;font-size:13px;letter-spacing:.5px;display:flex;align-items:center;justify-content:center}
.center{left:0;width:1200px;text-align:center}

/* header */
.site-header{left:0;top:0;width:1200px;height:146px;background:var(--navy)}
.brand{left:70px;top:32px;display:flex;align-items:center;gap:12px}
.brand-dot{width:44px;height:44px;border-radius:50%;background:var(--orange)}
.brand-name{font-family:"Montserrat",Arial,sans-serif;font-weight:800;font-size:26px;color:var(--orange)}
.top-contact{top:29px;height:30px;display:flex;align-items:center;gap:14px;color:var(--white);font-family:"Montserrat",Arial,sans-serif;font-weight:600;font-size:14px}
.top-contact .ico{width:30px;height:30px;border-radius:50%;background:var(--orange);display:flex;align-items:center;justify-content:center}
.nav-item{top:103px;font-family:"Montserrat",Arial,sans-serif;font-weight:700;font-size:13px;color:var(--white);letter-spacing:.3px}
.nav-item.active{color:var(--orange)}
.nav-bar{left:338px;top:138px;width:80px;height:7px;background:var(--orange)}

/* hero */
.hero{left:0;top:146px;width:1200px;height:519px;background:linear-gradient(115deg,#3a2a22 0%,#7a4a30 30%,#a86a45 48%,#5a4a4a 70%,#2a2c3a 100%)}
.hero-title{top:352px;font-family:"Montserrat",Arial,sans-serif;font-weight:900;font-size:40px;line-height:49px;color:var(--white)}
.hero-dot{top:617px;width:32px;height:6px;background:var(--white)}
.hero-dot.on{background:var(--orange)}

/* welcome */
.welcome-title{top:712px;font-size:24px}
.welcome-text{left:75px;top:760px;width:1050px;text-align:center;font-size:15.5px;line-height:27px}

/* bands */
.bands{left:0;top:0}

/* services */
.what-title{top:1042px;font-size:24px}
.what-sub{top:1095px;font-size:15.5px}
.card{top:1141px;width:330px;height:278px;background:var(--white);text-align:center}
.card svg{position:absolute;left:132px;top:24px}
.card-title{position:absolute;left:0;top:118px;width:100%;font-family:"Montserrat",Arial,sans-serif;font-weight:700;font-size:20px;line-height:27px;color:var(--navy)}
.card-note{display:block;font-family:"Arimo",Arial,sans-serif;font-size:14px;color:#888;font-weight:700}
.card .btn{left:90px;top:212px;width:150px;height:44px}

/* blog */
.blog-title{left:75px;top:1608px;font-size:24px}
.blog-arrows{left:1085px;top:1610px}
.post-img{top:1676px;width:195px;height:150px}
.post-title{top:1672px;font-family:"Montserrat",Arial,sans-serif;font-weight:700;font-size:16px;color:var(--navy)}
.post-text{top:1700px;width:310px;font-size:14.5px;line-height:26px}
.post-link{top:1805px;font-family:"Montserrat",Arial,sans-serif;font-weight:700;font-size:13.5px;color:var(--orange)}

/* testimonials */
.clients-title{top:1980px;font-size:24px}
.quote-mark{top:2042px;width:60px;height:60px;border-radius:50%;background:var(--orange)}
.quote-mark svg{position:absolute;left:16px;top:18px}
.quote-text{top:2124px;width:490px;text-align:center;font-size:15.5px;line-height:27px}
.quote-name{top:2220px;width:490px;text-align:center;font-family:"Montserrat",Arial,sans-serif;font-weight:700;font-size:13px;color:var(--navy)}
.t-dot{top:2278px;width:11px;height:11px;border-radius:50%;background:#999}
.t-dot.on{background:var(--orange)}

/* contact */
.contact-title{left:75px;top:2437px;font-size:24px}
.location-title{left:391px;top:2437px;font-size:24px}
.firm{left:75px;top:2494px;font-family:"Montserrat",Arial,sans-serif;font-weight:700;font-size:13.5px;color:var(--orange)}
.address{left:75px;top:2518px;font-size:14.5px;line-height:27px;color:#333}
.contact-line{left:75px;display:flex;align-items:center;gap:18px;font-size:14.5px;color:#333}
.contact-line svg{width:14px}
.contact-btn{left:75px;top:2712px;width:152px;height:44px}
.map{left:391px;top:2497px;width:734px;height:260px;background:linear-gradient(135deg,#cfe0b8 0%,#e6ead8 45%,#d8e4c4 70%,#b9cfe6 100%)}

/* footer */
.footer-nav{left:75px;top:2908px;font-family:"Montserrat",Arial,sans-serif;font-size:11.5px;color:#ddd;letter-spacing:.3px}
.footer-nav span{margin:0 7px;color:#999}
.copyright{left:75px;top:2950px;font-size:11.5px;color:#bbb}
.legal{left:75px;top:2973px;font-size:11.5px;color:#bbb}
.follow{left:928px;top:2938px;font-family:"Montserrat",Arial,sans-serif;font-weight:700;font-size:13px;color:var(--white)}
.social{left:928px;top:2966px;display:flex;gap:18px}
.social i{display:block;width:18px;height:18px;border-radius:50%;background:#bdbdbd}
</style>
</head>
<body>

<!-- background bands -->
<svg class="abs bands" width="1200" height="3041" aria-hidden="true">
  <polygon points="0,918 1200,1050 1200,1580 0,1450" fill="var(--grey-band)"/>
  <polygon points="0,1978 1200,1895 1200,2325 0,2415" fill="var(--grey-band)"/>
  <polygon points="0,2777 1200,2909 1200,3041 0,3041" fill="var(--footer)"/>
</svg>

<!-- header -->
<header class="abs site-header">
  <div class="abs brand"><span class="brand-dot"></span><span class="brand-name">TolVex</span></div>
  <div class="abs top-contact" style="left:728px">
    <span class="ico"><svg width="14" height="14" viewBox="0 0 24 24"><path fill="#fff" d="M6.6 10.8a15 15 0 006.6 6.6l2.2-2.2a1 1 0 011-.25 11.4 11.4 0 003.6.57 1 1 0 011 1V20a1 1 0 01-1 1A17 17 0 013 4a1 1 0 011-1h3.5a1 1 0 011 1c0 1.25.2 2.45.57 3.57a1 1 0 01-.25 1z"/></svg></span>
    1-800-555-0142
  </div>
  <div class="abs top-contact" style="left:908px">
    <span class="ico"><svg width="14" height="12" viewBox="0 0 24 18"><rect width="24" height="18" rx="2" fill="#fff"/><path d="M1 2l11 8 11-8" stroke="#f5a83a" stroke-width="2" fill="none"/></svg></span>
    hello@tolvex-mail.net
  </div>
  <nav>
    <span class="abs nav-item active" style="left:357px">HOME</span>
    <span class="abs nav-item" style="left:442px">ABOUT US</span>
    <span class="abs nav-item" style="left:557px">SERVICES</span>
    <span class="abs nav-item" style="left:667px">BLOG</span>
    <span class="abs nav-item" style="left:746px">CLIENTS</span>
    <span class="abs nav-item" style="left:847px">NEWS</span>
    <span class="abs nav-item" style="left:930px">CAREERS</span>
    <span class="abs nav-item" style="left:1036px">CONTACT US</span>
  </nav>
  <div class="abs nav-bar"></div>
</header>

<!-- hero -->
<section class="abs hero" role="img" aria-label="Two professionals wearing VR headsets over a glowing city model of buildings"></section>
<h1 class="abs center hero-title">Virtual Building and Construction<br>Building Information Modelling</h1>
<span class="abs hero-dot on" style="left:517px"></span>
<span class="abs hero-dot" style="left:561px"></span>
<span class="abs hero-dot" style="left:606px"></span>
<span class="abs hero-dot" style="left:651px"></span>

<!-- welcome -->
<h2 class="abs center heading welcome-title">WELCOME TO OUR WEBSITE</h2>
<p class="abs welcome-text">Aliquam molestie, mi et imperdiet euismod, dui purus auctor tellus, et interdum lacus lectus et ante. Sed accumsan sollicitudin sapien, sit amet adipiscing turpis gravida ac. In congue, neque ac lobortis volutpat, libero mauris varius mi, vitae suscipit ipsum ligula vitae risus. Duis aliquam nibh a dui iaculis viverra id a velit. Vivamus egestas risus in magna varius commodo. Sed semper viverra egestas.<br>Etiam pretium porttitor lectus, vel ornare neque porta volutpat.</p>
<span class="btn" style="left:525px;top:894px;width:150px;height:43px">READ MORE</span>

<!-- what we do -->
<h2 class="abs center heading what-title">WHAT WE DO</h2>
<p class="abs center what-sub">Aliquam molestie, mi et imperdiet euismod, dui purus auctor tellus, et interdum lacus lectus et ante.</p>

<article class="abs card" style="left:75px">
  <svg width="66" height="70" viewBox="0 0 66 70"><rect x="14" y="0" width="38" height="70" fill="#555"/><g fill="#fff"><rect x="20" y="8" width="8" height="7"/><rect x="38" y="8" width="8" height="7"/><rect x="20" y="22" width="8" height="7"/><rect x="38" y="22" width="8" height="7"/><rect x="20" y="36" width="8" height="7"/><rect x="38" y="36" width="8" height="7"/><rect x="27" y="54" width="12" height="16"/></g></svg>
  <h3 class="card-title">Virtual Building &amp;<br>Construction Building<br>Information Modelling</h3>
  <span class="btn">READ MORE</span>
</article>
<article class="abs card" style="left:434px">
  <svg width="80" height="70" viewBox="0 0 80 70"><rect x="10" y="12" width="60" height="40" rx="3" fill="none" stroke="#555" stroke-width="5"/><rect x="0" y="56" width="80" height="6" rx="2" fill="#555"/></svg>
  <h3 class="card-title">Training and Production<br>Work for Strukta<span class="card-note">(Quorvane application )</span></h3>
  <span class="btn">READ MORE</span>
</article>
<article class="abs card" style="left:797px">
  <svg width="80" height="70" viewBox="0 0 80 70"><rect x="27" y="4" width="26" height="14" rx="3" fill="none" stroke="#555" stroke-width="5"/><rect x="2" y="16" width="76" height="52" rx="6" fill="#555"/><g fill="#fff"><rect x="18" y="16" width="4" height="52"/><rect x="58" y="16" width="4" height="52"/></g></svg>
  <h3 class="card-title" style="top:130px">BIM Production &amp;<br>Coordination Services</h3>
  <span class="btn">READ MORE</span>
</article>

<!-- blog -->
<h2 class="abs heading blog-title">BLOG POSTS</h2>
<svg class="abs blog-arrows" width="42" height="22" viewBox="0 0 42 22" aria-label="Previous and next"><path d="M12 3L4 11l8 8M30 3l8 8-8 8" stroke="#444" stroke-width="2.5" fill="none"/></svg>

<div class="abs post-img" style="left:75px;background:linear-gradient(135deg,#0e2a4a,#2b6ea0 55%,#e0a040)" role="img" aria-label="Businessman touching a glowing digital city network"></div>
<h3 class="abs post-title" style="left:292px">NAM FERMENTUM VESTIBULUM</h3>
<p class="abs post-text" style="left:292px">Aliquam molestie, mi et imperdiet euismod, dui purus auctor tellus, et interdum lacus lectus et ante turpis in odio blandit ac interdum lorem euismod..</p>
<span class="abs post-link" style="left:292px">Continue Reading</span>

<div class="abs post-img" style="left:614px;background:linear-gradient(135deg,#d9dcdc,#9aa2a4 50%,#e8e6e0)" role="img" aria-label="Two colleagues working together at a desk with a laptop"></div>
<h3 class="abs post-title" style="left:831px">NAM FERMENTUM VESTIBULUM</h3>
<p class="abs post-text" style="left:831px">Aliquam molestie, mi et imperdiet euismod, dui purus auctor tellus, et interdum lacus lectus et ante a nibh eget turpis in odio blandit ac interdum lorem euismod..</p>
<span class="abs post-link" style="left:831px">Continue Reading</span>

<!-- testimonials -->
<h2 class="abs center heading clients-title">WHAT OUR CLIENT SAYS..</h2>
<div class="abs quote-mark" style="left:300px"><svg width="28" height="24" viewBox="0 0 28 24"><path fill="#fff" d="M0 12C0 4 4 0 10 0v5c-3 0-4 2-4 5h6v14H0zM16 12c0-8 4-12 10-12v5c-3 0-4 2-4 5h6v14H16z"/></svg></div>
<div class="abs quote-mark" style="left:838px"><svg width="28" height="24" viewBox="0 0 28 24"><path fill="#fff" d="M0 12C0 4 4 0 10 0v5c-3 0-4 2-4 5h6v14H0zM16 12c0-8 4-12 10-12v5c-3 0-4 2-4 5h6v14H16z"/></svg></div>
<p class="abs quote-text" style="left:75px">Aliquam molestie, mi et imperdiet euismod, dui purus auctor tellus, et interdum lacus lectus et ante a nibh eget turpis vehicula tempus ac sed massa egestas risus in magna varius commodo..”</p>
<p class="abs quote-text" style="left:613px">Aliquam molestie, mi et imperdiet euismod, dui purus auctor tellus, et interdum lacus lectus et ante a nibh eget turpis vehicula tempus ac sed massa egestas risus in magna varius commodo..”</p>
<span class="abs quote-name" style="left:75px">-NAME HEADING</span>
<span class="abs quote-name" style="left:613px">-NAME HEADING</span>
<span class="abs t-dot on" style="left:575px"></span>
<span class="abs t-dot" style="left:595px"></span>
<span class="abs t-dot" style="left:614px"></span>

<!-- contact -->
<h2 class="abs heading contact-title">CONTACT INFO</h2>
<h2 class="abs heading location-title">LOCATION</h2>
<span class="abs firm">TOLVEX BIM CONSULTING</span>
<p class="abs address">412 Brinwell<br>Road,Glasgow, G12 4PX</p>
<div class="abs contact-line" style="top:2582px"><svg viewBox="0 0 24 24" height="14"><path fill="#333" d="M6.6 10.8a15 15 0 006.6 6.6l2.2-2.2a1 1 0 011-.25 11.4 11.4 0 003.6.57 1 1 0 011 1V20a1 1 0 01-1 1A17 17 0 013 4a1 1 0 011-1h3.5a1 1 0 011 1c0 1.25.2 2.45.57 3.57a1 1 0 01-.25 1z"/></svg>1-800-555-0142</div>
<div class="abs contact-line" style="top:2615px"><svg viewBox="0 0 24 18" height="11"><rect width="24" height="18" rx="2" fill="#333"/><path d="M1 2l11 8 11-8" stroke="#fff" stroke-width="2" fill="none"/></svg>hello@tolvex-mail.net</div>
<div class="abs contact-line" style="top:2648px"><svg viewBox="0 0 16 24" height="14"><path fill="#333" d="M8 0a8 8 0 00-8 8c0 6 8 16 8 16s8-10 8-16a8 8 0 00-8-8zm0 11a3 3 0 110-6 3 3 0 010 6z"/></svg>Map Location</div>
<span class="btn contact-btn">CONTACT US</span>
<div class="abs map" role="img" aria-label="Road map of the Glasgow area with a location marker"></div>

<!-- footer -->
<footer>
  <p class="abs footer-nav">HOME<span>/</span>ABOUT US<span>/</span>SERVICES<span>/</span>BLOG<span>/</span>CLIENTS<span>/</span>NEWS<span>/</span>CAREERS<span>/</span>CONTACT US</p>
  <p class="abs copyright">Copyright © 2017. Company Name. All Rigt Reserved</p>
  <p class="abs legal">Privacy Policy &nbsp;|&nbsp; Terms Of Services</p>
  <span class="abs follow">FOLLOW US:</span>
  <div class="abs social" aria-label="Social links"><i></i><i></i><i></i><i></i><i></i><i></i></div>
</footer>

</body>
</html>
```